Flyer Tally Your Own Ledger

Hi
Can you please design me a DL Flyer for: Tally Your Own Ledger
Info:
Starting a new Business ?
Want to save on bookkeeping fees for your existing business?

You can now save 1000's off bookkeeping fees by Doing it Yourself.

Using our Bookkeeper software you simply key in the information as you go.

We offer one on one training, backup and support.
We can assist you with BAS Preparation and Payrol Advice.

Add Modules as required:
Point of Sale Module
Jobs Management Module
Website Intergration Module

Fee set up assistance and training.

Lets get the ball rolling: 1300 462 518
www.tyoleg.com.au
admin@tyoleg.com.au (use the logo thing you made)

Target Market(s)

Small Business

Colors
ec1f27
f04a50
f59296
fcdcdc
ffffff

Requirements
Nice to have
• image/s related to bookkeeping

```html
<!DOCTYPE html>
<html lang="en">
<head>
<meta charset="utf-8">
<title>Tally Your Own Ledger – DL Flyer</title>
<link href="https://fonts.googleapis.com/css2?family=Montserrat:wght@400;500;600;700;800&display=swap" rel="stylesheet">
<style>
:root{
  --red:#ec1f27;
  --red-soft:#f04a50;
  --pink:#f59296;
  --blush:#fcdcdc;
  --white:#ffffff;
  --ink:#2b2b2b;
  --text:#3a3a3a;
  --dark:#2d2d2f;
  --header:#efefef;
  --stage:#e6e6e6;
}
*{margin:0;padding:0;box-sizing:border-box}
html,body{width:758px;height:1200px;overflow:hidden}
body{background:var(--stage);font-family:'Montserrat',sans-serif;color:var(--text);position:relative}
.flyer{position:absolute;top:248px;width:330px;height:703px;background:var(--white);box-shadow:0 2px 6px rgba(0,0,0,.15);overflow:hidden}
.flyer--front{left:29px}
.flyer--back{left:399px}
.masthead{position:absolute;left:0;top:0;width:100%;height:68px;background:var(--header);display:flex;align-items:center;justify-content:center;gap:7px}
.masthead__dot{width:14px;height:14px;border-radius:50%;background:var(--red)}
.masthead__name{font-weight:600;font-size:16px;color:var(--red);letter-spacing:-.2px}
.hero{position:absolute;left:0;width:100%}
.hero--desk{top:68px;height:380px;border-top:2px solid var(--red);border-bottom:3px solid #6b6b6b;background:linear-gradient(135deg,#3b3b3b 0%,#d9dde0 35%,#f4f6f7 55%,#8fb7cc 75%,#d8d2c6 100%)}
.hero--coins{top:70px;height:292px;border-top:2px solid #6b6b6b;border-bottom:3px solid var(--red);background:linear-gradient(180deg,#d9a7a6 0%,#c7b8c9 22%,#efe3c9 45%,#cfb57a 70%,#9c8e74 100%)}
.headline{position:absolute;left:32px;top:470px;font-weight:800;font-size:23px;line-height:25px;color:var(--ink);padding-left:9px;border-left:4px solid var(--red)}
.headline span{display:block}
.headline .accent{color:var(--red);font-weight:700}
.info-label{position:absolute;left:31px;top:550px;font-size:12px;font-weight:500;color:var(--ink)}
.info-label::after{content:"";display:block;width:17px;height:1px;background:var(--ink);margin-top:4px}
.info-list{position:absolute;left:31px;top:582px;width:270px;list-style:none}
.info-list li{display:flex;gap:14px;font-size:7.6px;line-height:9.5px;margin-bottom:12px}
.info-list li::before{content:"";flex:0 0 12px;height:12px;border:1.5px solid var(--red-soft);border-radius:3px}
.info-list b{font-weight:700}
.footer-band{position:absolute;left:0;bottom:0;width:100%;height:30px;background:var(--dark);display:flex;align-items:center}
.footer-band__phone{height:100%;width:132px;background:var(--red);clip-path:polygon(0 0,88% 0,100% 100%,0 100%);display:flex;align-items:center;gap:6px;padding-left:31px;color:var(--white);font-weight:700;font-size:10.5px}
.footer-band__links{color:var(--white);font-size:5.6px;padding-left:8px;display:flex;gap:6px;align-items:center}
.footer-band__links i{display:inline-block;width:5px;height:4px;background:var(--red);margin-right:3px}
.footer-band__links i.round{border-radius:50%;height:5px}
.intro{position:absolute;left:31px;top:378px;font-size:8.4px;line-height:11.5px;font-weight:600;color:var(--ink)}
.intro .accent{color:var(--red);font-weight:700}
.bullets{position:absolute;left:31px;top:412px;width:250px;list-style:none}
.bullets li{display:flex;gap:14px;font-size:7.8px;line-height:9.5px;margin-bottom:11px}
.bullets li::before{content:"";flex:0 0 11px;height:11px;margin-top:3px;border-radius:50%;border:1.5px solid var(--red)}
.modules-title{position:absolute;left:31px;top:481px;font-size:9.4px;font-weight:600;color:var(--ink)}
.modules-title .accent{color:var(--red);font-weight:700}
.modules{position:absolute;left:31px;top:511px;width:280px;display:grid;grid-template-columns:146px 134px;row-gap:20px}
.module{display:flex;align-items:center;gap:9px;font-size:7.8px;line-height:9.5px;font-weight:600;color:var(--ink)}
.module::before{content:"";flex:0 0 15px;height:15px;border-radius:50%;background:var(--red);box-shadow:0 0 0 2px var(--white),0 0 0 3px #9a9a9a}
.cta{position:absolute;left:0;top:611px;width:100%;text-align:center;font-weight:600;font-size:13px;color:var(--ink);letter-spacing:.2px}
.cta .accent{color:var(--red);font-weight:700}
.contact-rule{position:absolute;left:0;top:637px;width:100%;display:flex;align-items:center;gap:8px;font-size:7.4px;color:var(--ink)}
.contact-rule::before,.contact-rule::after{content:"";height:1px;background:var(--ink);flex:1}
.contact-rule span{display:flex;align-items:center;gap:4px;margin:0 6px}
.web{position:absolute;left:0;top:658px;width:100%;text-align:center;font-weight:600;font-size:22px;color:#555}
.web .accent{color:var(--red)}
.base-bar{position:absolute;left:0;bottom:0;width:100%;height:7px;background:var(--dark)}
</style>
</head>
<body>

<section class="flyer flyer--front">
  <header class="masthead"><span class="masthead__dot"></span><span class="masthead__name">Tally Your Own Ledger</span></header>
  <div class="hero hero--desk" role="img" aria-label="Photo of hands reviewing printed bar charts and spreadsheets on a desk with a phone and pen"></div>
  <h1 class="headline"><span class="accent">TALLY YOUR</span><span>OWN LEDGER</span></h1>
  <p class="info-label">INFO:</p>
  <ul class="info-list">
    <li>Starting a new Business ?</li>
    <li>Want to save on bookkeeping fees for your existing business?</li>
    <li><span>You can now save <b>1000's</b> off bookkeeping fees by Doing it Yourself.</span></li>
  </ul>
  <footer class="footer-band">
    <div class="footer-band__phone">
      <svg width="9" height="9" viewBox="0 0 24 24" fill="#fff"><path d="M6.6 10.8a15 15 0 0 0 6.6 6.6l2.2-2.2a1 1 0 0 1 1-.25 11.4 11.4 0 0 0 3.6.57 1 1 0 0 1 1 1V20a1 1 0 0 1-1 1A17 17 0 0 1 3 4a1 1 0 0 1 1-1h3.5a1 1 0 0 1 1 1c0 1.25.2 2.45.57 3.57a1 1 0 0 1-.25 1z"/></svg>
      1300 462 518
    </div>
    <div class="footer-band__links"><span><i></i>admin@tyoleg.com.au</span><span>|</span><span><i class="round"></i>www.tyoleg.com.au</span></div>
  </footer>
</section>

<section class="flyer flyer--back">
  <header class="masthead"><span class="masthead__dot"></span><span class="masthead__name">Tally Your Own Ledger</span></header>
  <div class="hero hero--coins" role="img" aria-label="Photo of wooden blocks marked asset and finance symbols resting on stacks of coins"></div>
  <p class="intro">USING OUR BOOKKEEPER SOFTWARE<br><span class="accent">YOU SIMPLY KEY IN THE INFORMATION AS YOU GO.</span></p>
  <ul class="bullets">
    <li>We offer one on one training, backup<br>and support.</li>
    <li>We can assist you with BAS Preparation and<br>Payrol Advice.</li>
  </ul>
  <p class="modules-title">ADD <span class="accent">MODULES :</span></p>
  <div class="modules">
    <div class="module">Point of Sale<br>Module</div>
    <div class="module">Website Intergration<br>Module</div>
    <div class="module">Jobs Management<br>Module</div>
    <div class="module">Fee set up assistance<br>and training</div>
  </div>
  <p class="cta">LETS GET THE <span class="accent">BALL ROLLING:</span></p>
  <div class="contact-rule">
    <span><svg width="7" height="7" viewBox="0 0 24 24" fill="#ec1f27"><path d="M6.6 10.8a15 15 0 0 0 6.6 6.6l2.2-2.2a1 1 0 0 1 1-.25 11.4 11.4 0 0 0 3.6.57 1 1 0 0 1 1 1V20a1 1 0 0 1-1 1A17 17 0 0 1 3 4a1 1 0 0 1 1-1h3.5a1 1 0 0 1 1 1c0 1.25.2 2.45.57 3.57a1 1 0 0 1-.25 1z"/></svg>1300 462 518</span>
    <span><svg width="7" height="6" viewBox="0 0 24 18" fill="#ec1f27"><path d="M0 0h24v18H0z"/><path d="M0 0l12 9 12-9" stroke="#fff" stroke-width="2" fill="none"/></svg>admin@tyoleg.com.au</span>
  </div>
  <p class="web">www.tyo<span class="accent">leg</span>.com.au</p>
  <div class="base-bar"></div>
</section>

</body>
</html>
```